label design for instant full cream powdered milk for pouch packing
brand nordvale logo and design as previously done by you for condensed
milk
wordings required
brand nordvale
instant full cream powdered milk
900 grms
have enclosed a idea design
of harbin milk
we want colours
white and blue red
as preferable colours
this is front of pouch
for the sides i will send you later
we urgently need the front
Updates

Colors
ffffff
ec2027
85cae6
33a6d7
0792cd

Requirements
Must have
• colours white blue red
• logo colours
• have enclosed dyeline file
• brand tobias
• we basically want to change this and use white ble and red basic colours same as harbin
• rest of wording follow brand tobias
• tobias is to be removed from all the text logos
• worings on side
• our brand and logo is in file 3 must follow exactly
• please remove vista crest details from information website
• replace with
• http://www.northernvaleoils.example
Nice to have
• Further to the below requests, instead of changing the shade of the purple back ground to ligher,
• please change the color of the wordings to white from blue.
Should not have
• 1. Please change font of Nordvale Logo to Font Albertus Medium
• Enclosed the picture for your reference.
• 2. Please refer to the uploaded file No. 2 QWMTR294LZBNDA (e). Logo appears on the left side also. Follow the same
• 3. Left side of the label has a black background, please change it to different colour
• 4. Right hand side, under Manufactured for column, please remove the Logo, just the drop is fine. You can refer to the enclosed file
• 5. On both sides reduce the shade of the purple back ground to lighter as the wordings are not clearly visible

```html
<!DOCTYPE html>
<html lang="en">
<head>
<meta charset="utf-8">
<title>Nordvale Full Cream Milk Powder – Front Label</title>
<link href="https://fonts.googleapis.com/css2?family=Open+Sans:wght@700;800&display=swap" rel="stylesheet">
<style>
  :root {
    --canvas: #ffffff;
    --sky-top: #1273e0;
    --sky-mid: #4fa3e6;
    --sky-low: #a9d6ef;
    --field: #5f9a34;
    --field-dark: #3f7424;
    --banner: #561185;
    --brand-red: #ec2027;
    --band-blue: #0d5db5;
    --milk: #f7f8fa;
    --milk-shade: #dfe3e8;
    --ink-dark: #1b1b1b;
    --white: #ffffff;
  }
  * { margin: 0; padding: 0; box-sizing: border-box; }
  html, body { width: 1200px; height: 1200px; overflow: hidden; background: var(--canvas); }
  .canvas { position: relative; width: 1200px; height: 1200px; }
  .label {
    position: absolute; left: 296px; top: 158px; width: 608px; height: 883px;
    overflow: hidden; font-family: "Open Sans", Arial, sans-serif;
  }
  .scene {
    position: absolute; inset: 0;
    background: linear-gradient(180deg, var(--sky-top) 0%, var(--sky-mid) 30%, var(--sky-low) 52%, #cfe6f0 56%, var(--field) 62%, var(--field-dark) 100%);
  }
  .shapes { position: absolute; inset: 0; }
  .brand-banner { position: absolute; left: 161px; top: 0; width: 286px; height: 252px; }
  .brand-name {
    position: absolute; left: 0; top: 88px; width: 608px;
    display: flex; align-items: center; justify-content: center; gap: 14px;
    color: var(--white); font-weight: 800; font-size: 50px; letter-spacing: 8px;
  }
  .brand-dot { width: 22px; height: 22px; border-radius: 50%; background: var(--white); flex: none; }
  .product-title {
    position: absolute; left: 0; top: 300px; width: 608px; text-align: center;
    color: var(--brand-red); font-weight: 700; font-size: 59px; line-height: 67px;
    -webkit-text-stroke: 3px var(--white); paint-order: stroke fill;
  }
  .enrichment {
    position: absolute; left: 46px; top: 795px;
    color: var(--white); font-weight: 700; font-size: 19px; line-height: 31px;
  }
  .net-weight {
    position: absolute; right: 38px; top: 830px;
    color: var(--ink-dark); font-weight: 700; font-size: 17px;
  }
</style>
</head>
<body>
<div class="canvas">
  <div class="label">
    <div class="scene" role="img" aria-label="Photo of a blue sky over a green pasture with a grazing dairy cow and farmhouses"></div>

    <svg class="shapes" width="608" height="883" viewBox="0 0 608 883">
      <defs>
        <radialGradient id="milkGlow" cx="0.5" cy="0.5" r="0.5">
          <stop offset="0" stop-color="var(--milk)"/>
          <stop offset="0.6" stop-color="var(--milk-shade)" stop-opacity="0.95"/>
          <stop offset="1" stop-color="var(--milk-shade)" stop-opacity="0"/>
        </radialGradient>
      </defs>
      <path d="M0,795 Q300,845 608,780 L608,883 L0,883 Z" fill="var(--band-blue)"/>
      <ellipse role="img" aria-label="Illustration of milk pouring and splashing into a full glass"
               cx="420" cy="700" rx="210" ry="230" fill="url(#milkGlow)"/>
    </svg>

    <svg class="brand-banner" viewBox="0 0 286 252" aria-hidden="true">
      <path d="M0,0 H286 V252 L143,222 L0,252 Z" fill="var(--banner)"/>
    </svg>
    <div class="brand-name"><span class="brand-dot"></span>NORDVALE</div>

    <h1 class="product-title">Full Cream<br>Milk Powder</h1>

    <p class="enrichment">Enriched with<br>Vitamin A, and D3</p>
    <p class="net-weight">Net Wt. 900g</p>
  </div>
</div>
</body>
</html>
```